Responsive Wordpress Site Design - Veterans Job Site

I need a re-design of my web page, www.pinnorahires.com. I want it to be Responsive so it looks great on mobile. I am a job recruiter for military veterans in the U.S. Here is a sample re-design site that a different developer just finished for me: http://pinnorahires.com/test/ I fired him because I got frustrated with his design abilities. But, this site is the general idea of what I want. I want the colors to be red, white and blue. I like a lot of white space so, big type, and video/pictures so it's easy on the eyes. I like this page: http://quillmarsporting.com/ . I do a lot with videos (that's how I present my veterans to companies, testimonials, job tips) so I would like to have a lot of video on the page. I want the home page to be one long scrolling page so it is easy to navigate on mobile and I can load it with keywords for SEO. I want the page to have a patriotic and powerful feel.

Target Market(s)

I have two audiences: Veterans looking for jobs and Companies looking to hire jobs. Right now I focus on the state of Connecticut, but next month I'm expanding to Massachusetts and I have plans to expand nationwide.

Industry/Entity Type

Marketing

Font styles to use
Sans Serif

Colors
ec1f27
0455a3
ffffff

Requirements
Must have
• Lots of Youtube videos...overviews of how the company works (I'll create this videos later, just use a placeholder for now), testimonials, job tips
• Social media feeds for Facebook and Twitter
• Big pictures
• Top section big and clear for Veterans to "Register Free"...this will bounce to my registration page...the most important goal of the site.
• Big and clear way for Companies to complete a form to request more information.
• Highlight videos of testimonials...the success stories
• Big headlines and text so the page is easy on the eyes and easy to read on a mobile phone.
• Lots of white space
• A professional look...want viewers to see the company as a strong
• I need the ability to edit the page when you're done....to add forms, additional pages, etc.
Nice to have
• see must haves
Should not have
• see must haves

```html
<!DOCTYPE html>
<html lang="en">
<head>
<meta charset="utf-8">
<title>Pinnora Hires – Great Jobs For Veterans</title>
<link href="https://fonts.googleapis.com/css2?family=Roboto:wght@300;400;500;700;900&display=swap" rel="stylesheet">
<style>
:root{
  --red:#ec1f27;
  --blue:#0455a3;
  --navy:#0c2f8f;
  --white:#ffffff;
  --ink:#333a45;
  --muted:#7a808a;
  --line:#e3e5e9;
  --soft:#f1f2f4;
  --feed-a:#3b5a9a;
  --feed-b:#2aa9e0;
  --footer:#262626;
  --footer-2:#1b1b1b;
}
*{box-sizing:border-box;margin:0;padding:0}
html,body{width:1200px;height:4265px;overflow:hidden}
body{font-family:'Roboto',Arial,sans-serif;color:var(--ink);background:var(--white);position:relative}
.wrap{width:1000px;margin:0 auto;position:relative}
a{color:inherit;text-decoration:none}

.topnav{height:46px;background:var(--navy)}
.topnav .wrap{display:flex;height:46px;align-items:stretch}
.topnav .item{color:#fff;font-size:12px;font-weight:500;text-transform:uppercase;padding:0 20px;display:flex;align-items:center;letter-spacing:.3px}
.topnav .item.active{background:var(--red)}
.topnav .call{margin-left:auto;background:var(--red);color:#fff;width:284px;display:flex;align-items:center;justify-content:center;gap:9px;font-size:15px}

.hero{height:517px;position:relative;overflow:hidden}
.hero .photo{position:absolute;inset:0;background:radial-gradient(ellipse at 50% 70%,#c9ccd1 0%,#a9adb4 45%,#8d9199 100%)}
.hero .people{position:absolute;left:340px;top:260px;width:520px;height:257px;background:linear-gradient(180deg,#6d6f74,#3e4049);border-radius:6px 6px 0 0}
.hero .brand{position:absolute;top:28px;left:0;right:0;text-align:center}
.hero .brand .name{display:inline-flex;align-items:center;gap:12px;font-size:40px;font-weight:900;color:var(--navy);text-transform:uppercase;letter-spacing:1px}
.hero .brand .dot{width:38px;height:38px;border-radius:50%;background:var(--red)}
.hero .brand .tag{font-size:11px;color:var(--navy);margin-top:2px}
.hero h1{position:absolute;top:150px;left:0;right:0;text-align:center;color:#fff;font-size:35px;font-weight:700;line-height:44px;text-shadow:0 2px 6px rgba(0,0,0,.35)}
.hero .arrow{position:absolute;top:240px;width:26px;height:36px;background:rgba(255,255,255,.55);display:flex;align-items:center;justify-content:center}
.hero .arrow.l{left:0}.hero .arrow.r{right:0}
.hero .dots{position:absolute;bottom:12px;left:0;right:0;display:flex;justify-content:center;gap:7px}
.hero .dots i{width:8px;height:8px;border-radius:50%;background:#fff;opacity:.6}
.hero .dots i:first-child{opacity:1}

.audience{height:91px;border-bottom:1px solid var(--line)}
.audience .wrap{display:flex;height:91px}
.aud{flex:1;display:flex;align-items:center;gap:30px;padding-left:86px}
.aud + .aud{border-left:1px solid var(--line);padding-left:74px}
.aud h2{font-size:35px;font-weight:700;line-height:34px;letter-spacing:.5px}
.aud p{font-size:12px;color:var(--muted)}
.aud.vet h2{color:var(--red)}
.aud.emp h2{color:var(--navy)}
.btn{display:inline-block;color:#fff;font-size:14px;font-weight:500;padding:10px 22px;border-radius:2px}
.btn.red{background:var(--red)}
.btn.navy{background:var(--navy)}
.btn.outline{background:#fff;border:1px solid var(--navy);color:var(--navy);font-size:12px;padding:8px 14px;border-radius:3px}

.recruit{height:663px;text-align:center;padding-top:80px}
.title{font-size:40px;font-weight:400;line-height:48px}
.title.red{color:var(--red)}
.title.navy{color:var(--navy)}
.lede{font-size:11.5px;line-height:19px;color:#555b66;width:880px;margin:0 auto}
.recruit .lede{margin-top:30px}
.recruit .lede + .lede{margin-top:18px}
.vidpair{display:flex;justify-content:center;gap:10px;margin-top:34px}
.thumb{position:relative;background:linear-gradient(135deg,#4a4d52,#1f2126)}
.recruit .thumb{width:236px;height:147px}
.play{position:absolute;left:50%;top:50%;width:40px;height:28px;margin:-14px 0 0 -20px;background:var(--red);border-radius:7px;display:flex;align-items:center;justify-content:center}
.recruit .btn{margin-top:38px;padding:11px 26px}

.spotlight{height:660px;background:var(--soft);text-align:center;padding-top:40px}
.spotlight .lede{margin-top:20px;width:700px}
.cards{display:flex;gap:29px;margin-top:24px;text-align:left}
.card{width:228px;height:412px;background:#fff;box-shadow:0 1px 3px rgba(0,0,0,.08)}
.card .img{height:151px}
.card .body{padding:20px 14px}
.card h3{font-size:12px;font-weight:700;color:#2f3540;text-transform:uppercase}
.card .loc{display:flex;gap:6px;margin-top:12px;font-size:12px;line-height:17px;color:var(--navy)}
.card .pay{font-size:12px;color:var(--navy);margin-top:12px}
.card .desc{font-size:10px;line-height:15px;color:var(--muted);margin-top:14px}
.card .btn{margin-top:20px}

.stats{height:213px;background:var(--navy);color:#fff}
.stats .wrap{display:flex;justify-content:space-between;padding-top:36px}
.stat{width:230px;text-align:center}
.stat b{display:block;font-size:48px;font-weight:500;line-height:58px}
.stat span{font-size:12px;line-height:17px;display:block;margin-top:6px}

.success{height:583px;text-align:center;padding-top:50px}
.success .pair{display:flex;gap:34px;margin-top:42px}
.success .col{width:483px}
.success .thumb{height:256px;text-align:left}
.vbar{position:absolute;left:0;right:0;top:0;height:24px;background:rgba(0,0,0,.55);color:#fff;font-size:11px;line-height:24px;padding-left:10px;white-space:nowrap;overflow:hidden}
.ctrl{position:absolute;left:0;right:0;bottom:0;height:22px;background:rgba(0,0,0,.75)}
.ctrl i{position:absolute;left:0;top:0;height:3px;width:18%;background:var(--red)}
.success .t1{background:linear-gradient(180deg,#8f2c31 0%,#e9e7e8 50%,#2b2f6b 100%)}
.success .t2{background:linear-gradient(180deg,#bcd7ec,#9dc3e2)}
.t2 .over{position:absolute;top:70px;left:0;right:0;text-align:center;color:var(--navy);font-size:30px;font-weight:900;line-height:38px}
.success p{font-size:11.5px;line-height:17px;color:#555b66;margin:14px 30px 0;text-align:center}
.success .btn{margin-top:22px;font-size:11px;text-transform:uppercase}

.quote{height:213px;background:var(--navy);color:#fff;text-align:center;padding-top:58px}
.quote blockquote{font-size:17px;font-style:italic;line-height:25px;width:780px;margin:0 auto}
.quote cite{display:block;font-style:normal;font-size:16px;font-weight:700;margin-top:18px}

.tips{height:526px;background:#f4f4f5;text-align:center;padding-top:60px}
.tips .title{letter-spacing:1px}
.tips .cards{margin-top:20px;gap:29px}
.tip{width:228px;height:364px;background:#fff;text-align:left;box-shadow:0 1px 3px rgba(0,0,0,.08)}
.tip .thumb{height:156px}
.tip .thumb .vbar{font-size:9px;height:18px;line-height:18px}
.tip p{font-size:11px;line-height:17px;color:#555b66;padding:18px 16px}

.social{height:242px;padding-top:14px}
.social .wrap{display:flex;gap:12px}
.feed{flex:1;height:214px;padding:0 8px 8px}
.feed.community{background:var(--feed-a)}
.feed.updates{background:var(--feed-b)}
.feed .hd{height:46px;display:flex;align-items:center;gap:10px;color:#fff;font-size:17px}
.feed .hd i{width:22px;height:22px;background:#fff;border-radius:2px;display:block}
.feed .box{background:#fff;height:160px;padding:14px 14px;font-size:11px;line-height:16px;color:#555b66}
.feed .box b{color:var(--navy);font-weight:500}
.feed .box small{display:block;color:var(--blue);margin-top:10px}

.stay{height:185px;text-align:center;padding-top:24px}
.stay .title{font-size:38px}
.stay p{font-size:11.5px;color:#555b66;margin-top:8px}
.signup{display:flex;justify-content:center;gap:12px;margin-top:22px}
.field{width:222px;height:32px;border:1px solid #cfd2d8;font-size:11px;color:#999;text-align:left;padding:9px 12px}
.signup .btn{background:var(--navy);padding:8px 20px;font-size:13px}

.footer{height:326px;background:var(--footer);color:#cfcfcf;position:relative}
.contactline{height:54px;display:flex;justify-content:center;align-items:center;gap:40px;font-size:13px;color:#fff;border-bottom:1px solid #3a3a3a}
.contactline span{display:flex;align-items:center;gap:8px}
.fcols{display:flex;gap:44px;padding-top:26px}
.fcol h4{font-size:11px;font-weight:500;color:#fff;text-transform:uppercase;margin-bottom:10px;letter-spacing:.4px}
.fcol li{list-style:none;font-size:10px;line-height:18px}
.fcol li::before{content:"› "}
.cform{width:330px;display:grid;grid-template-columns:1fr 1fr;gap:6px}
.cform div{height:20px;background:#5a5a5a;font-size:9px;color:#bbb;padding:4px 8px}
.cform .send{width:46px;background:#4caf50;color:#fff;grid-column:1}
.newsl{width:150px;height:26px;background:#fff;font-size:9px;color:#999;padding:7px 8px;position:relative}
.newsl::after{content:"";position:absolute;right:0;top:0;width:26px;height:26px;background:#ccc}
.fbottom{position:absolute;left:0;right:0;bottom:0;height:70px;background:var(--footer-2)}
.fbottom .wrap{display:flex;justify-content:space-between;align-items:center;height:70px;font-size:10px}
.fbottom .links{line-height:16px}
.icons{display:flex;gap:8px}
.icons i{width:24px;height:24px;border-radius:50%;background:#4a4a4a;display:block}
.icons i.b{background:var(--blue)}.icons i.r{background:var(--red)}
</style>
</head>
<body>

<nav class="topnav">
  <div class="wrap">
    <a class="item active">Home</a>
    <a class="item">Register Free</a>
    <a class="item">Testimonials</a>
    <a class="item">Hire a Veteran</a>
    <a class="item">About Us</a>
    <a class="item">Support</a>
    <a class="call"><svg width="14" height="14" viewBox="0 0 24 24"><path fill="#fff" d="M6.6 10.8a15 15 0 0 0 6.6 6.6l2.2-2.2a1 1 0 0 1 1-.25 11.4 11.4 0 0 0 3.6.57 1 1 0 0 1 1 1V20a1 1 0 0 1-1 1A17 17 0 0 1 3 4a1 1 0 0 1 1-1h3.5a1 1 0 0 1 1 1c0 1.25.2 2.45.57 3.57a1 1 0 0 1-.25 1z"/></svg>Call us : (203) 555-0142</a>
  </div>
</nav>

<header class="hero">
  <div class="photo" role="img" aria-label="Soft grey background photo of soldiers standing in formation"></div>
  <div class="people" role="img" aria-label="Three veterans in work uniforms and business attire"></div>
  <div class="brand">
    <div class="name"><span class="dot"></span>Pinnora Hires</div>
    <div class="tag">Great Employees For Companies... Great Jobs For Veterans</div>
  </div>
  <h1>Great Employees For Companies...<br>Great Jobs For Veterans</h1>
  <div class="arrow l"><svg width="10" height="14"><path d="M8 1 2 7l6 6" stroke="#fff" stroke-width="2" fill="none"/></svg></div>
  <div class="arrow r"><svg width="10" height="14"><path d="m2 1 6 6-6 6" stroke="#fff" stroke-width="2" fill="none"/></svg></div>
  <div class="dots"><i></i><i></i><i></i></div>
</header>

<section class="audience">
  <div class="wrap">
    <div class="aud vet"><div><h2>VETERANS</h2><p>Need a great job?</p></div><a class="btn red">Register Free</a></div>
    <div class="aud emp"><div><h2>EMPLOYERS</h2><p>Need a great employee?</p></div><a class="btn navy">Learn more</a></div>
  </div>
</section>

<section class="recruit">
  <h2 class="title red">We recruit awesome veterans!</h2>
  <p class="lede">Pinnora Hires is a free job placement and coaching service for military veterans. We work with companies throughout Connecticut in a wide range of industries, including manufacturing, sales and marketing, healthcare, finance, security and technology. Our goal is to place our veterans into great jobs and onto a meaningful career path. We think of the companies we work with as partners, and provide our business community with the support they need to hire great employees and to make certain our veterans receive every opportunity they greatly deserve.</p>
  <p class="lede">We have a team of experienced and dedicated recruiters and job coaches who work one-on-one with our veterans and help companies to hire top-notch military veterans transitioning to civilian life. If you're looking for a rewarding career and possess the skills, desire, and confidence to add enormous value, please register so we can promote you to hiring managers.</p>
  <div class="vidpair">
    <div class="thumb" role="img" aria-label="Video thumbnail: veteran introduction"><span class="play"><svg width="12" height="12"><path d="M2 1l9 5-9 5z" fill="#fff"/></svg></span></div>
    <div class="thumb" role="img" aria-label="Video thumbnail: veteran introduction"><span class="play"><svg width="12" height="12"><path d="M2 1l9 5-9 5z" fill="#fff"/></svg></span></div>
  </div>
  <a class="btn red">Register Free</a>
</section>

<section class="spotlight">
  <div class="wrap">
    <h2 class="title navy">Spotlight Jobs</h2>
    <p class="lede">We need to fill dozens of jobs this month in manufacturing, sales, customer service, IT management, security, healthcare, and accounting. Listings change daily as jobs are filled and new ones are posted so please <b>register</b> even if you don't see anything that interests your right now.</p>
    <div class="cards">
      <article class="card">
        <div class="img" role="img" aria-label="Service member saluting in front of a flag" style="background:linear-gradient(135deg,#b3424a,#6e7a8c)"></div>
        <div class="body">
          <h3>Warehouse &amp; Manufacturing</h3>
          <div class="loc"><svg width="10" height="14" viewBox="0 0 10 14"><path d="M5 0a5 5 0 0 0-5 5c0 4 5 9 5 9s5-5 5-9a5 5 0 0 0-5-5zm0 7a2 2 0 1 1 0-4 2 2 0 0 1 0 4z" fill="#0c2f8f"/></svg><span>Meriden, Hartford, Windsor, Waterbury, Bridgeport, New Haven</span></div>
          <div class="pay">Salary: $12 - $14/hour</div>
          <p class="desc">All shifts available, excellent medical plan, manufacturing, warehouse experience a plus but not required.</p>
          <a class="btn outline">Apply Now</a>
        </div>
      </article>
      <article class="card">
        <div class="img" role="img" aria-label="Deck crew working on an aircraft carrier" style="background:linear-gradient(135deg,#7f96b0,#c99a2e)"></div>
        <div class="body">
          <h3>Warehouse &amp; Manufacturing</h3>
          <div class="loc"><svg width="10" height="14" viewBox="0 0 10 14"><path d="M5 0a5 5 0 0 0-5 5c0 4 5 9 5 9s5-5 5-9a5 5 0 0 0-5-5zm0 7a2 2 0 1 1 0-4 2 2 0 0 1 0 4z" fill="#0c2f8f"/></svg><span>Meriden, Hartford, Windsor, Waterbury, Bridgeport, New Haven</span></div>
          <div class="pay">Salary: $12 - $14/hour</div>
          <p class="desc">All shifts available, excellent medical plan, manufacturing, warehouse experience a plus but not required.</p>
          <a class="btn outline">Apply Now</a>
        </div>
      </article>
      <article class="card">
        <div class="img" role="img" aria-label="Sailors in orange gear on a flight deck" style="background:linear-gradient(135deg,#c9602c,#3a4660)"></div>
        <div class="body">
          <h3>Warehouse &amp; Manufacturing</h3>
          <div class="loc"><svg width="10" height="14" viewBox="0 0 10 14"><path d="M5 0a5 5 0 0 0-5 5c0 4 5 9 5 9s5-5 5-9a5 5 0 0 0-5-5zm0 7a2 2 0 1 1 0-4 2 2 0 0 1 0 4z" fill="#0c2f8f"/></svg><span>Meriden, Hartford, Windsor, Waterbury, Bridgeport, New Haven</span></div>
          <div class="pay">Salary: $12 - $14/hour</div>
          <p class="desc">All shifts available, excellent medical plan, manufacturing, warehouse experience a plus but not required.</p>
          <a class="btn outline">Apply Now</a>
        </div>
      </article>
      <article class="card">
        <div class="img" role="img" aria-label="Naval warship at sea" style="background:linear-gradient(180deg,#b8c3cf,#5b6a7d)"></div>
        <div class="body">
          <h3>Warehouse &amp; Manufacturing</h3>
          <div class="loc"><svg width="10" height="14" viewBox="0 0 10 14"><path d="M5 0a5 5 0 0 0-5 5c0 4 5 9 5 9s5-5 5-9a5 5 0 0 0-5-5zm0 7a2 2 0 1 1 0-4 2 2 0 0 1 0 4z" fill="#0c2f8f"/></svg><span>Meriden, Hartford, Windsor, Waterbury, Bridgeport, New Haven</span></div>
          <div class="pay">Salary: $12 - $14/hour</div>
          <p class="desc">All shifts available, excellent medical plan, manufacturing, warehouse experience a plus but not required.</p>
          <a class="btn outline">Apply Now</a>
        </div>
      </article>
    </div>
  </div>
</section>

<section class="stats">
  <div class="wrap">
    <div class="stat"><b>72%</b><span>of veterans we present to client companies get interviewed</span></div>
    <div class="stat"><b>51%</b><span>of veterans interviewed receive job offers</span></div>
    <div class="stat"><b>96%</b><span>of client companies satisfied after hiring our veterans</span></div>
    <div class="stat"><b>200%</b><span>more candidates screened by clients resulting in better hiring decision</span></div>
  </div>
</section>

<section class="success">
  <div class="wrap">
    <h2 class="title navy">Success story of the week</h2>
    <div class="pair">
      <div class="col">
        <div class="thumb t1" role="img" aria-label="Testimonial video: veteran in front of an American flag">
          <div class="vbar">Testimonial - Marcus Bellamy - Coast Guard Veteran</div>
          <span class="play"><svg width="12" height="12"><path d="M2 1l9 5-9 5z" fill="#fff"/></svg></span>
          <div class="ctrl"><i></i></div>
        </div>
        <p>Congratulations to U.S. Coast Guard Veteran, Marcus Bellamy, from Bridgeport, CT. Marcus recently landed a great job with Pinnora Hires client, Upton Precision, one of Connecticut's premier commercial printers.</p>
        <a class="btn outline">Veterans speak out</a>
      </div>
      <div class="col">
        <div class="thumb t2" role="img" aria-label="Overview video for employers">
          <div class="vbar">PINNORA HIRES: Great Employees For Companies...Great Jobs For Veterans</div>
          <div class="over">Great Employees For<br>Companies...<br>Great Jobs For Veterans</div>
          <span class="play"><svg width="12" height="12"><path d="M2 1l9 5-9 5z" fill="#fff"/></svg></span>
          <div class="ctrl"><i></i></div>
        </div>
        <p>Put Pinnora Hires to work for your business and we'll help you recruit some amazing employees who will work hard to make your business successful. We'll save you time evaluating potential candidates and help your company...</p>
        <a class="btn outline">Read more</a>
      </div>
    </div>
  </div>
</section>

<section class="quote">
  <blockquote>“ You made it so easy to hire two new employees — and good ones! I really liked being able to evaluate the veterans' intro videos before deciding which ones I wanted to interview. ”</blockquote>
  <cite>Carol D., Manager, Bethel, CT</cite>
</section>

<section class="tips">
  <div class="wrap">
    <h2 class="title navy">JOB SEARCH TIPS</h2>
    <div class="cards">
      <article class="tip">
        <div class="thumb" role="img" aria-label="Job search tip video with a program director"><div class="vbar">Job Search Tip - Diane Walters</div><span class="play"><svg width="12" height="12"><path d="M2 1l9 5-9 5z" fill="#fff"/></svg></span></div>
        <p>Diane Walters, Director of Program Services at Lantern House Shelter in Stamford, CT, shares some useful job interview advice for military veterans and explains how important it is for job seekers to have confidence during their search.</p>
      </article>
      <article class="tip">
        <div class="thumb" role="img" aria-label="Job search tip video with a speaker"><div class="vbar">Ending Gaps in Employment</div><span class="play"><svg width="12" height="12"><path d="M2 1l9 5-9 5z" fill="#fff"/></svg></span></div>
        <p>Diane Walters, Director of Program Services at Lantern House Shelter in Stamford, CT, shares some useful job interview advice for military veterans and explains how important it is for job seekers to have confidence during their search.</p>
      </article>
      <article class="tip">
        <div class="thumb" role="img" aria-label="Tip of the day video about unemployment gaps" style="background:linear-gradient(135deg,#e9e9ea,#bfc3c9)"><div class="vbar">Tip Of The Day - Unemployment Gap</div><span class="play"><svg width="12" height="12"><path d="M2 1l9 5-9 5z" fill="#fff"/></svg></span></div>
        <p>Diane Walters, Director of Program Services at Lantern House Shelter in Stamford, CT, shares some useful job interview advice for military veterans and explains how important it is for job seekers to have confidence during their search.</p>
      </article>
      <article class="tip">
        <div class="thumb" role="img" aria-label="Job search tip video with a program director"><div class="vbar">Job Search Tip - Diane Walters</div><span class="play"><svg width="12" height="12"><path d="M2 1l9 5-9 5z" fill="#fff"/></svg></span></div>
        <p>Diane Walters, Director of Program Services at Lantern House Shelter in Stamford, CT, shares some useful job interview advice for military veterans and explains how important it is for job seekers to have confidence during their search.</p>
      </article>
    </div>
  </div>
</section>

<section class="social">
  <div class="wrap">
    <div class="feed community">
      <div class="hd"><i></i>Community Feed</div>
      <div class="box"><b>Curabitur augue ex, elementum non viverra pharetra, pellentesque vel nunc. Cras quis risus viverra, dapibus neque at, malesuada ante.</b><br><br>Sed elementum odio nunc, gravida mattis lorem interdum semper. Etiam conse quat lacus a felis viverra eget rhoncus massa ullamcorper.<small>Reply · Comment · Share</small></div>
    </div>
    <div class="feed updates">
      <div class="hd"><i></i>Latest Updates</div>
      <div class="box"><b>Pinnora Hires</b> @pinnorahires<br>Jul 8, 2015<br><br>Sed elementum odio nunc, gravida mattis lorem interdum semper. Etiam conse quat lacus a felis viverra eget rhoncus massa ullamcorper.<small>Reply · Share · Save</small></div>
    </div>
  </div>
</section>

<section class="stay">
  <h2 class="title navy">STAY IN THE LOOP!</h2>
  <p>Join our confidential network and be the first know about job listings for Connecticut military veterans. We value your privacy!</p>
  <div class="signup"><div class="field">Name</div><div class="field">E-mail</div><a class="btn">Sign up</a></div>
</section>

<footer class="footer">
  <div class="contactline">
    <span><svg width="13" height="13" viewBox="0 0 24 24"><path fill="#fff" d="M6.6 10.8a15 15 0 0 0 6.6 6.6l2.2-2.2a1 1 0 0 1 1-.25 11.4 11.4 0 0 0 3.6.57 1 1 0 0 1 1 1V20a1 1 0 0 1-1 1A17 17 0 0 1 3 4a1 1 0 0 1 1-1h3.5a1 1 0 0 1 1 1c0 1.25.2 2.45.57 3.57a1 1 0 0 1-.25 1z"/></svg>Contact us today (203) 555-0142</span>
    <span><svg width="14" height="11" viewBox="0 0 14 11"><rect x=".5" y=".5" width="13" height="10" fill="none" stroke="#fff"/><path d="m1 1 6 5 6-5" stroke="#fff" fill="none"/></svg>hello@pinnorahires.com</span>
  </div>
  <div class="wrap fcols">
    <div class="fcol"><h4>Contact Us</h4>
      <div class="cform"><div>Name</div><div>Phone</div><div>E-mail</div><div>Message</div><div class="send">Submit</div></div>
    </div>
    <div class="fcol"><h4>Quick Links</h4><ul><li>Home</li><li>Register Free</li><li>Testimonials</li><li>Hire A Veteran</li><li>About Us</li></ul></div>
    <div class="fcol"><h4>More</h4><ul><li>Refer a Buddy</li><li>Supporters</li><li>FAQ</li><li>Job Tips</li></ul></div>
    <div class="fcol"><h4>More</h4><ul><li>Refer a Buddy</li><li>Supporters</li><li>FAQ</li><li>Job Tips</li></ul></div>
    <div class="fcol"><h4>Newsletter</h4><div class="newsl">E-mail</div></div>
  </div>
  <div class="fbottom">
    <div class="wrap">
      <div class="links">Home &nbsp;|&nbsp; Contact us &nbsp;|&nbsp; About us &nbsp;|&nbsp; Live Chat<br>Copyright © 2015 Pinnora Hires. All rights reserved.</div>
      <div class="icons"><i class="b"></i><i class="b"></i><i class="r"></i><i class="b"></i><i class="b"></i><i></i><i></i></div>
    </div>
  </div>
</footer>

</body>
</html>
```